Harbor Oncology Partners Patient Referral Card

We need a 3.75" wide by 8.25" long patient referral card that a physician will fill out to refer their patient to Harbor Oncology Partners. The front of the card will have our logo on top, followed by contact information, a map that shows the office location and then there will be descriptive text at the bottom. On the back side, there will be a headshot photo with a brief bio of Dr. Marcus Whitfield. The address for the office is: 4185 N. Larkspur, Fairhaven, WA 98412. The office phone number is 253.417.5820 and the website address is: harboroncologypartners.com

Target Market(s)

Physicians and medical staff

Font styles to use
Serif

Colors
34a7d8
33b8a4
9bcb3c

Requirements
Must have
• A map of the office location and two text boxes for descriptive language about services, and a photo and bio of Dr. Marcus Whitfield
Nice to have
• Clean and distinct design that is eye catching
Should not have
• Flowery or bold colors that distract from the content and purpose of the card

```html
<!DOCTYPE html>
<html lang="en">
<head>
<meta charset="utf-8">
<title>Harbor Oncology Partners – Referral Card</title>
<link rel="stylesheet" href="https://fonts.googleapis.com/css2?family=Libre+Baskerville&family=Playfair+Display:wght@400&family=Montserrat:wght@500&family=Roboto:wght@400;700&display=swap">
<style>
  :root {
    --teal: #24b3bd;
    --green: #4cb963;
    --ink: #111111;
    --dark: #0e0e0e;
    --map-dark: #262626;
    --stage: #e6e7e8;
    --muted: #8a8a8a;
    --white: #ffffff;
  }
  * { margin: 0; padding: 0; box-sizing: border-box; }
  html, body { width: 1200px; height: 1200px; overflow: hidden; }
  body { background: var(--stage); position: relative; font-family: "Roboto", Arial, sans-serif; }

  .card { position: absolute; width: 440px; height: 968px; overflow: hidden; }
  .card-front { left: 98px; top: 100px; background: var(--white); }
  .card-back { left: 620px; top: 160px; background: var(--dark); color: var(--white); }
  .card-bg { position: absolute; inset: 0; }

  .brand { position: absolute; left: 0; right: 0; top: 56px; height: 160px; }
  .brand-dot { position: absolute; left: 58px; top: 48px; width: 64px; height: 64px; border-radius: 50%; background: var(--teal); }
  .brand-name {
    position: absolute; left: 140px; top: 0;
    font-family: "Libre Baskerville", Georgia, serif; font-weight: 400; font-size: 40px; line-height: 52px;
    letter-spacing: 3px; color: var(--teal);
  }
  .tagline {
    position: absolute; left: 0; right: 0; top: 224px; text-align: center;
    font-family: "Montserrat", Arial, sans-serif; font-weight: 500; font-size: 16px;
    letter-spacing: 8px; color: #333;
  }
  .front-phone { position: absolute; left: 0; right: 0; top: 280px; text-align: center; font-weight: 700; font-size: 31px; color: var(--ink); }
  .front-web { position: absolute; left: 0; right: 0; top: 322px; text-align: center; font-weight: 700; font-size: 19px; color: var(--ink); }

  .map-area {
    position: absolute; left: 40px; top: 420px; width: 390px; height: 215px;
    background: var(--map-dark); border-radius: 4px;
  }

  .referral-title {
    position: absolute; left: 0; right: 0; top: 676px; text-align: center;
    font-family: "Playfair Display", "Times New Roman", serif; font-weight: 400; font-size: 50px; color: var(--ink);
  }
  .field { position: absolute; left: 42px; width: 358px; border-bottom: 2px solid var(--white); font-size: 20px; color: #2b3a3c; padding-bottom: 6px; }
  .field-name { top: 758px; }
  .field-date { top: 816px; }
  .field-time { top: 872px; }

  .headshot { position: absolute; left: 0; top: 0; width: 440px; height: 524px; background: linear-gradient(180deg, #d2d4d4 0%, #8c9090 40%, #2e3030 100%); clip-path: path("M0 0 H440 V460 Q260 520 0 524 Z"); }

  .doc-name { position: absolute; left: 0; right: 0; top: 546px; text-align: center; font-weight: 400; font-size: 36px; color: var(--teal); }
  .doc-name small { font-size: 24px; }
  .doc-role { position: absolute; left: 0; right: 0; top: 590px; text-align: center; font-size: 23px; }
  .bio { position: absolute; left: 30px; right: 30px; text-align: center; font-size: 18px; line-height: 23.5px; }
  .bio-one { top: 638px; }
  .bio-two { top: 756px; }
  .divider { position: absolute; left: 20px; right: 20px; top: 822px; height: 2px; background: linear-gradient(90deg, transparent, var(--teal) 50%, transparent); }
  .back-phone { position: absolute; left: 0; right: 0; top: 834px; text-align: center; font-size: 36px; color: var(--teal); }
  .back-address { position: absolute; left: 0; right: 0; top: 878px; text-align: center; font-size: 21px; color: var(--teal); }
  .back-web { position: absolute; left: 0; right: 0; top: 908px; text-align: center; font-size: 19px; font-weight: 700; color: var(--muted); }
</style>
</head>
<body>

<section class="card card-front">
  <svg class="card-bg" width="440" height="968" viewBox="0 0 440 968" aria-hidden="true">
    <defs>
      <linearGradient id="referral-fill" x1="0" y1="0" x2="0" y2="1">
        <stop offset="0" stop-color="#d9eff1"/>
        <stop offset="1" stop-color="#74c4cc"/>
      </linearGradient>
    </defs>
    <path d="M0 398 Q240 414 440 352 L440 680 Q250 612 0 664 Z" fill="#1f1f1f"/>
    <path d="M0 402 Q240 414 440 356" fill="none" stroke="var(--green)" stroke-width="9"/>
    <path d="M40 398 Q260 398 440 338" fill="none" stroke="var(--teal)" stroke-width="6"/>
    <path d="M0 650 Q230 592 440 662 L440 968 L0 968 Z" fill="#9ea8aa"/>
    <path d="M0 660 Q230 604 440 676 L440 968 L0 968 Z" fill="url(#referral-fill)"/>
  </svg>

  <div class="brand">
    <span class="brand-dot"></span>
    <div class="brand-name">Harbor<br>Oncology<br>Partners</div>
  </div>
  <p class="tagline">RADIATION ONCOLOGY</p>
  <p class="front-phone">253-417-5820</p>
  <p class="front-web">www.harboroncologypartners.com</p>

  <div class="map-area" role="img" aria-label="Street map showing the office at 4185 N. Larkspur, Fairhaven, WA 98412"></div>

  <h2 class="referral-title">REFERRAL</h2>
  <p class="field field-name">NAME</p>
  <p class="field field-date">DATE</p>
  <p class="field field-time">TIME</p>
</section>

<section class="card card-back">
  <div class="headshot" role="img" aria-label="Headshot photo of Dr. Marcus Whitfield in a dark suit"></div>
  <svg class="card-bg" width="440" height="968" viewBox="0 0 440 968" aria-hidden="true">
    <path d="M0 520 Q250 518 440 460" fill="none" stroke="var(--teal)" stroke-width="4"/>
  </svg>

  <h1 class="doc-name">Marcus Whitfield, <small>MD PhD</small></h1>
  <p class="doc-role">Radiation Oncology</p>
  <p class="bio bio-one">Dr. Whitfield has 12+ years of experience treating cancer patients. He trained at Lakemont Cancer Institute, a top cancer center in the United States.</p>
  <p class="bio bio-two">He trained at Lakemont Cancer Institute,<br>one of the world's leading cancer centers.</p>
  <div class="divider"></div>
  <p class="back-phone">253-417-5820</p>
  <p class="back-address">4185 N. Larkspur, Fairhaven, WA 98412.</p>
  <p class="back-web">www.harboroncologypartners.com</p>
</section>

</body>
</html>
```